Yard sign for Chimney Buisness

I am looking for a 18 Tall x 24" wide yard sign design incorporating our logo/name. We want the signs to stand out and be readable from a distance. only want our logo/business name and website on the sign . www.sootwardenspro.com

Target Market(s)

homeowners

Requirements
Must have
• logo/buisness name
• website
• must be visable at a distance and readable

```html
<!DOCTYPE html>
<html lang="en">
<head>
<meta charset="utf-8">
<title>Soot Wardens — Yard Sign Options</title>
<link rel="stylesheet" href="https://fonts.googleapis.com/css2?family=Bebas+Neue&family=Cinzel:wght@500&display=swap">
<style>
  :root {
    --brand-red: #a00000;
    --charcoal: #333333;
    --paper: #ffffff;
  }
  * { box-sizing: border-box; margin: 0; padding: 0; }
  html, body { width: 1200px; height: 965px; overflow: hidden; background: var(--paper); }
  .sheet { position: relative; width: 1200px; height: 965px; }

  .sign {
    position: absolute;
    width: 540px;
    height: 404px;
    display: grid;
    grid-template-rows: 314px 74px 16px;
    overflow: hidden;
  }
  .sign--tl { left: 39px;  top: 60px; }
  .sign--tr { left: 622px; top: 59px; }
  .sign--bl { left: 39px;  top: 501px; }
  .sign--br { left: 623px; top: 502px; }
  .sign--outlined { border: 1px solid var(--charcoal); }

  .sign__brand {
    display: flex;
    flex-direction: column;
    align-items: center;
    padding-top: 49px;
  }
  .brand-square {
    width: 147px;
    height: 147px;
    border: 15px solid currentColor;
  }
  .brand-name {
    margin-top: 26px;
    font-family: "Cinzel", serif;
    font-weight: 500;
    font-size: 41px;
    line-height: 1;
    letter-spacing: 1px;
    white-space: nowrap;
  }
  .brand-tagline {
    margin-top: 4px;
    width: 373px;
    display: flex;
    align-items: center;
    gap: 8px;
    font-family: "Cinzel", serif;
    font-weight: 500;
    font-size: 19px;
    line-height: 1;
    letter-spacing: 1px;
    white-space: nowrap;
  }
  .brand-tagline::before,
  .brand-tagline::after {
    content: "";
    flex: 1;
    height: 3px;
    background: currentColor;
  }

  .sign__web {
    display: flex;
    align-items: center;
    justify-content: center;
    font-family: "Bebas Neue", sans-serif;
    font-size: 52px;
    letter-spacing: 1.5px;
    line-height: 1;
    padding-top: 4px;
    white-space: nowrap;
  }

  .theme-red-top   .sign__brand { background: var(--brand-red); color: var(--paper); }
  .theme-red-top   .sign__web   { background: var(--paper); color: var(--charcoal); }
  .theme-red-top   .sign__strip { background: var(--brand-red); }

  .theme-white-dark .sign__brand { background: var(--paper); color: var(--charcoal); }
  .theme-white-dark .sign__web   { background: var(--brand-red); color: var(--paper); }
  .theme-white-dark .sign__strip { background: var(--paper); }

  .theme-white-red .sign__brand { background: var(--paper); color: var(--brand-red); }
  .theme-white-red .sign__web   { background: var(--brand-red); color: var(--paper); }
  .theme-white-red .sign__strip { background: var(--paper); }

  .theme-red-dark  .sign__brand { background: var(--brand-red); color: var(--paper); }
  .theme-red-dark  .sign__web   { background: var(--charcoal); color: var(--paper); }
  .theme-red-dark  .sign__strip { background: var(--brand-red); }
</style>
</head>
<body>
<main class="sheet">
  <section class="sign sign--tl theme-red-top">
    <div class="sign__brand"><div class="brand-square"></div><p class="brand-name">SOOT WARDENS</p><p class="brand-tagline">INC 1989</p></div>
    <p class="sign__web">WWW.SOOTWARDENSPRO.COM</p>
    <div class="sign__strip"></div>
  </section>

  <section class="sign sign--tr sign--outlined theme-white-dark">
    <div class="sign__brand"><div class="brand-square"></div><p class="brand-name">SOOT WARDENS</p><p class="brand-tagline">INC 1989</p></div>
    <p class="sign__web">WWW.SOOTWARDENSPRO.COM</p>
    <div class="sign__strip"></div>
  </section>

  <section class="sign sign--bl sign--outlined theme-white-red">
    <div class="sign__brand"><div class="brand-square"></div><p class="brand-name">SOOT WARDENS</p><p class="brand-tagline">INC 1989</p></div>
    <p class="sign__web">WWW.SOOTWARDENSPRO.COM</p>
    <div class="sign__strip"></div>
  </section>

  <section class="sign sign--br theme-red-dark">
    <div class="sign__brand"><div class="brand-square"></div><p class="brand-name">SOOT WARDENS</p><p class="brand-tagline">INC 1989</p></div>
    <p class="sign__web">WWW.SOOTWARDENSPRO.COM</p>
    <div class="sign__strip"></div>
  </section>
</main>
</body>
</html>
```